Business card for my new company (Accounting firm)

I need a business card for my new business Brightwell Advisory and Ledger SA. Our services are accounting, tax, audit and financial management. Our customers are small companies, start-ups and new companies. The final design has to show financial security, trust and growth. Please find our logo attached to the business card. Text for the business card: Brightwell Advisory and Ledger SA Tomas Varenholt Director and Founder Certified Accountant Tel. 022 418 57 34 tv@clairevalconseil.ch www.clairevalconseil.ch Rue des Vergières 27 1201 Geneva
Target Market(s)
Our customers are small companies, start-ups and new companies.
Industry/Entity Type
Finance And Accounting
Contact Information for Business Card
Claireval Conseil et Comptes SA
Tomas Varenholt
Directeur et Fondateur
Expert-comptable diplômé
Tél. 022 418 57 34
tv@clairevalconseil.ch
www.clairevalconseil.ch
Rue des Vergières 27
1201 Genève

```html
<!DOCTYPE html>
<html lang="fr">
<head>
<meta charset="utf-8">
<title>Claireval Conseil et Comptes – Carte de visite</title>
<link href="https://fonts.googleapis.com/css2?family=Raleway:wght@400;500;700&display=swap" rel="stylesheet">
<style>
  :root {
    --page: #e4e5e7;
    --paper: #f4f4f4;
    --sky: #2fa8d8;
    --navy: #1b5f8e;
    --ink: #333a40;
    --white: #ffffff;
  }
  * { box-sizing: border-box; margin: 0; padding: 0; }
  html, body { width: 1200px; height: 960px; overflow: hidden; }
  body {
    background: var(--page);
    font-family: "Raleway", Arial, sans-serif;
    position: relative;
  }
  .card {
    position: absolute;
    left: 270px;
    width: 660px;
    height: 377px;
    border-radius: 22px;
    overflow: hidden;
    box-shadow: 0 6px 18px rgba(0,0,0,0.25);
  }
  .card-front { top: 73px; background: var(--paper); }
  .card-back { top: 508px; background: var(--navy); }
  .card-shapes { position: absolute; inset: 0; }
  .brand {
    position: absolute;
    display: flex;
    align-items: center;
    gap: 10px;
    font-weight: 700;
    letter-spacing: 1px;
  }
  .brand-dot { border-radius: 50%; flex: none; }
  .brand-front { left: 57px; top: 120px; color: var(--ink); font-size: 28px; }
  .brand-front .brand-dot { width: 18px; height: 18px; background: var(--sky); }
  .brand-back { left: 0; right: 0; top: 160px; justify-content: center; color: var(--white); font-size: 46px; gap: 16px; }
  .brand-back .brand-dot { width: 28px; height: 28px; background: var(--white); }
  .holder { position: absolute; left: 57px; top: 208px; color: var(--white); }
  .holder-name { font-size: 20px; font-weight: 700; color: var(--navy); letter-spacing: 0.3px; margin-bottom: 4px; }
  .holder-role { font-size: 15px; line-height: 19px; }
  .address, .contact { position: absolute; top: 304px; color: var(--white); font-size: 15px; line-height: 19.5px; }
  .address { left: 58px; }
  .contact { right: 92px; text-align: right; }
  .icons { position: absolute; left: 575px; top: 305px; display: flex; flex-direction: column; gap: 5.5px; }
  .icons svg { width: 14px; height: 14px; }
</style>
</head>
<body>
  <section class="card card-front">
    <svg class="card-shapes" viewBox="0 0 660 377" aria-hidden="true">
      <polygon points="0,196 501,196 452,283 0,283" fill="var(--sky)"/>
      <path d="M0,291 L452,291 L514,178 Q530,152 546,178 L660,360 L660,377 L0,377 Z" fill="var(--navy)"/>
    </svg>
    <div class="brand brand-front"><span class="brand-dot"></span>CLAIREVAL</div>
    <div class="holder">
      <p class="holder-name">TOMAS VARENHOLT</p>
      <p class="holder-role">Directeur et Fondateur</p>
      <p class="holder-role">Expert - Comptable Diplômé</p>
    </div>
    <div class="address">
      <p>Claireval Conseil et Comptes SA</p>
      <p>Rue des Vergières 27</p>
      <p>1201 Genève</p>
    </div>
    <div class="contact">
      <p>022 418 57 34</p>
      <p>tv@clairevalconseil.ch</p>
      <p>www.clairevalconseil.ch</p>
    </div>
    <div class="icons" aria-hidden="true">
      <svg viewBox="0 0 16 16"><path d="M4 1.5l2.3 3-1.4 1.6c.9 2 2.6 3.7 4.6 4.6l1.6-1.4 3 2.3-1.4 2.4C7 13.6 2.4 9 1.6 3z" fill="none" stroke="#fff" stroke-width="1.3" stroke-linejoin="round"/></svg>
      <svg viewBox="0 0 16 16"><rect x="1.5" y="3.5" width="13" height="9" fill="none" stroke="#fff" stroke-width="1.3"/><path d="M1.5 3.5l6.5 5.5 6.5-5.5" fill="none" stroke="#fff" stroke-width="1.3"/></svg>
      <svg viewBox="0 0 16 16" fill="none" stroke="#fff" stroke-width="1.2"><circle cx="8" cy="8" r="6.3"/><ellipse cx="8" cy="8" rx="2.8" ry="6.3"/><path d="M1.7 8h12.6M2.8 4.8h10.4M2.8 11.2h10.4"/></svg>
    </div>
  </section>

  <section class="card card-back">
    <div class="brand brand-back"><span class="brand-dot"></span>CLAIREVAL</div>
  </section>
</body>
</html>
```